Business Card for a mobile physiotherapy company

I need a layout for a business card for a mobile physiotherapy company.
Slogan is "Mobile Physiotherapy - Your Road To Recovery"
Phone number is 867-555-0142
Email VardenTherapy@postnest.ca (subject to change with website)
Website www.VardenTherapy.ca
My name and credentials: Luke Varden Luke Varden, BSc(kin), MPT, CAFCI, IMS
Information maybe included: Direct Billing, Services including Physiotherapy, IMS, acupuncture
Maybe include facebook and instagram logos
One side with the logo clean and sharp
Other side with details, try not to look too busy, keep everything concise

```html
<!DOCTYPE html>
<html lang="en">
<head>
<meta charset="utf-8">
<title>Varden Therapy – Business Card</title>
<link href="https://fonts.googleapis.com/css2?family=Tinos:wght@400;700&family=Lato:wght@400&display=swap" rel="stylesheet">
<style>
  :root {
    --page-bg: #e8e8ea;
    --navy: #2b4770;
    --forest: #0c574b;
    --seal: #f1f0f2;
    --white: #ffffff;
    --rule: rgba(255, 255, 255, 0.45);
  }
  * { margin: 0; padding: 0; box-sizing: border-box; }
  html, body {
    width: 1200px;
    height: 900px;
    overflow: hidden;
    background: var(--page-bg);
  }
  .card {
    position: absolute;
    left: 110px;
    top: 146px;
    width: 980px;
    height: 607px;
    background: var(--navy);
    overflow: hidden;
    box-shadow: 0 14px 40px rgba(0, 0, 0, 0.18);
  }
  .card__side-band {
    position: absolute;
    left: 664px;
    top: 0;
    width: 316px;
    height: 100%;
    background: var(--forest);
  }
  .seal {
    position: absolute;
    left: 400px;
    top: 35px;
    width: 526px;
    height: 526px;
    border-radius: 50%;
    background: var(--seal);
    display: flex;
    align-items: center;
    justify-content: center;
  }
  .seal__name {
    color: var(--navy);
    font-family: "Lato", Arial, sans-serif;
    font-weight: 400;
    font-size: 46px;
    line-height: 1;
    white-space: nowrap;
  }
  .holder {
    position: absolute;
    left: 57px;
    top: 92px;
    color: var(--white);
    font-family: "Tinos", "Times New Roman", serif;
  }
  .holder__name {
    font-size: 33px;
    font-weight: 700;
    line-height: 1;
    text-transform: uppercase;
  }
  .holder__credentials {
    margin-top: 12px;
    font-size: 25px;
    font-weight: 400;
    line-height: 1;
  }
  .social-rule {
    position: absolute;
    left: 57px;
    top: 209px;
    width: 340px;
    height: 44px;
  }
  .social-rule__line {
    position: absolute;
    top: 21px;
    height: 1.5px;
    background: var(--rule);
  }
  .social-rule__line--left { left: 0; width: 115px; }
  .social-rule__line--right { left: 215px; width: 125px; }
  .social-rule__dot {
    position: absolute;
    top: 1px;
    width: 42px;
    height: 42px;
    border-radius: 50%;
    background: var(--white);
  }
  .social-rule__dot--first { left: 122px; }
  .social-rule__dot--second { left: 168px; }
  .services {
    position: absolute;
    left: 57px;
    top: 276px;
    list-style: none;
    color: var(--white);
    font-family: "Lato", Arial, sans-serif;
    font-size: 27px;
    line-height: 36.5px;
  }
  .services li::before {
    content: "";
    display: inline-block;
    width: 15px;
    height: 15px;
    border-radius: 50%;
    background: var(--white);
    margin-right: 9px;
    vertical-align: 2px;
  }
  .divider {
    position: absolute;
    left: 57px;
    top: 407px;
    width: 340px;
    height: 1.5px;
    background: var(--rule);
  }
  .contacts {
    position: absolute;
    left: 57px;
    top: 426px;
    list-style: none;
    color: var(--white);
    font-family: "Lato", Arial, sans-serif;
    font-size: 27px;
    line-height: 36.5px;
  }
  .contacts li {
    display: flex;
    align-items: center;
  }
  .contacts svg {
    width: 24px;
    height: 24px;
    margin-right: 9px;
    flex: none;
  }
</style>
</head>
<body>
  <div class="card">
    <div class="card__side-band"></div>

    <div class="seal">
      <div class="seal__name">Varden Therapy</div>
    </div>

    <div class="holder">
      <div class="holder__name">Luke Varden</div>
      <div class="holder__credentials">BSC(KIN), MPT, CAFCI, IMS</div>
    </div>

    <div class="social-rule">
      <span class="social-rule__line social-rule__line--left"></span>
      <span class="social-rule__dot social-rule__dot--first"></span>
      <span class="social-rule__dot social-rule__dot--second"></span>
      <span class="social-rule__line social-rule__line--right"></span>
    </div>

    <ul class="services">
      <li>Direct Billing</li>
      <li>Physiotherapy</li>
      <li>IMS | acupuncture</li>
    </ul>

    <div class="divider"></div>

    <ul class="contacts">
      <li>
        <svg viewBox="0 0 24 24" aria-hidden="true"><path fill="#fff" d="M3 9c0-3 4-5 9-5s9 2 9 5v1.5h-4.5V8.5c-1.5-.6-3-.8-4.5-.8s-3 .2-4.5.8v2H3z"/><path fill="#fff" d="M6 12h12l2 8H4z"/><circle cx="12" cy="16" r="2.2" fill="#2b4770"/></svg>
        867-555-0142
      </li>
      <li>
        <svg viewBox="0 0 24 24" aria-hidden="true"><rect x="2" y="5" width="20" height="14" fill="#fff"/><path d="M2.5 5.5 12 13l9.5-7.5" fill="none" stroke="#2b4770" stroke-width="1.6"/></svg>
        VardenTherapy@postnest.ca
      </li>
      <li>
        <svg viewBox="0 0 24 24" aria-hidden="true"><circle cx="12" cy="12" r="10" fill="#fff"/><path d="M7 7c2 1 3 0 4 2s-2 3 0 5 1 4 1 6M15 5c-1 2 1 3 3 3s2 3 1 5" fill="none" stroke="#2b4770" stroke-width="1.6"/></svg>
        www.VardenTherapy.ca
      </li>
    </ul>
  </div>
</body>
</html>
```